Business card design Needed for new logo / Construction business, home extensions and new builds

We need a business card design using our new logo files which i will attach to this project :)

We are a small construction business specialising in home extensions, new builds and property development. We are very ambitious and would appreciate professional and elegant designs for our new business card.

Very serious about using the services on MakerQuarry and recently acquired our new logo from here :)

Please get involved, i will feedback when i can as i am very busy but can respond daily, thanks

Target Market(s)

People that want to build onto their houses, new building developments or adding too their existing property

Industry/Entity Type

Construction

Contact Information for Business Card

Renwick Tolliver Construction, Lionel Ashby (Managing Director), Tel 07822254961, email - info@renwick-tolliver, www.renwick-tolliver.co.uk

Colors

Designer to choose colors to be used in the design.

Requirements
Must have
• I like a deep grey on the back please. A lot of you have provided black from and back, try mixing things up a little. The black looks cool 😎 Thanks

```html
<!DOCTYPE html>
<html lang="en">
<head>
<meta charset="utf-8">
<title>Renwick Tolliver Construction — Business Card</title>
<link rel="stylesheet" href="https://fonts.googleapis.com/css2?family=Cinzel:wght@500&family=Lato:wght@400&display=swap">
<style>
  :root {
    --stage: #242424;
    --card-front: #1b1b1b;
    --card-back: #3a3b3d;
    --gold: #d4a22a;
    --gold-light: #e9c25a;
    --text-light: #ececec;
  }
  * { box-sizing: border-box; margin: 0; padding: 0; }
  html, body {
    width: 1200px; height: 875px; overflow: hidden;
    background: var(--stage);
  }
  .stage {
    width: 1200px; height: 875px;
    display: flex; flex-direction: column;
    align-items: center; justify-content: center; gap: 40px;
  }
  .card {
    width: 680px; height: 388px;
    border-radius: 18px;
    box-shadow: 0 18px 40px rgba(0,0,0,.45);
    position: relative;
  }

  /* Front */
  .card--front {
    background: var(--card-front);
    display: flex; align-items: center; justify-content: center;
  }
  .brand {
    display: flex; align-items: center; gap: 18px;
  }
  .brand__square {
    width: 22px; height: 22px; background: var(--gold); flex: none;
  }
  .brand__name {
    font-family: "Cinzel", serif; font-weight: 500;
    color: var(--gold); font-size: 34px; letter-spacing: 2px;
    text-transform: uppercase; text-align: center; line-height: 1.25;
  }
  .brand__name small { display: block; font-size: 24px; letter-spacing: 4px; }

  /* Back */
  .card--back {
    background: var(--card-back);
    display: flex; align-items: center; padding: 0 50px;
  }
  .back__brand {
    width: 230px; flex: none;
    font-family: "Cinzel", serif; font-weight: 500;
    color: var(--gold); font-size: 21px; letter-spacing: 1.5px;
    text-transform: uppercase; line-height: 1.4; text-align: center;
  }
  .back__divider {
    width: 2px; height: 190px; margin: 0 36px; flex: none;
    background: linear-gradient(var(--gold-light), var(--gold));
  }
  .contact { min-width: 0; }
  .contact__name {
    font-family: "Cinzel", serif; font-weight: 500;
    color: var(--gold); font-size: 27px; letter-spacing: 1px;
    text-transform: uppercase; white-space: nowrap;
  }
  .contact__role {
    font-family: "Lato", sans-serif; color: var(--text-light);
    font-size: 16px; margin: 4px 0 22px;
  }
  .contact__list { list-style: none; }
  .contact__item {
    display: flex; align-items: center; gap: 12px;
    font-family: "Lato", sans-serif; color: var(--text-light);
    font-size: 16px; margin-bottom: 8px; white-space: nowrap;
  }
  .contact__icon { width: 16px; height: 16px; flex: none; }
</style>
</head>
<body>
<main class="stage">
  <section class="card card--front" aria-label="Card front">
    <div class="brand">
      <span class="brand__square"></span>
      <h1 class="brand__name">Renwick Tolliver<small>Construction</small></h1>
    </div>
  </section>

  <section class="card card--back" aria-label="Card back">
    <div class="back__brand">Renwick Tolliver Construction</div>
    <div class="back__divider"></div>
    <div class="contact">
      <h2 class="contact__name">Lionel Ashby</h2>
      <p class="contact__role">Managing Director</p>
      <ul class="contact__list">
        <li class="contact__item">
          <svg class="contact__icon" viewBox="0 0 16 16" aria-hidden="true"><path fill="#d4a22a" d="M3.5 1.5l2.5 2.8-1.4 1.6c.8 1.8 2.3 3.3 4.1 4.1l1.6-1.4 2.8 2.5-1.5 2.3C6.5 13.2 2.8 9.5 1.2 3.4z"/></svg>
          07822254961
        </li>
        <li class="contact__item">
          <svg class="contact__icon" viewBox="0 0 16 16" aria-hidden="true"><rect x="1" y="3" width="14" height="10" fill="#d4a22a"/><path d="M1 3l7 5.5L15 3" fill="none" stroke="#3a3b3d" stroke-width="1.3"/></svg>
          info@renwick-tolliver.co.uk
        </li>
        <li class="contact__item">
          <svg class="contact__icon" viewBox="0 0 16 16" aria-hidden="true"><circle cx="8" cy="8" r="7" fill="#d4a22a"/><path d="M1 8h14M8 1c-3 3.5-3 10.5 0 14M8 1c3 3.5 3 10.5 0 14" fill="none" stroke="#3a3b3d" stroke-width="1"/></svg>
          renwick-tolliver.co.uk
        </li>
      </ul>
    </div>
  </section>
</main>
</body>
</html>
```